We are a recruitment company based in Norwich/Cambridge England.
I have included our company logo which we want to remain the same.

What we are looking for is a new creative Business card which will really stand out!!

Contact Information for Business Card

Harriet Dunmore
email: Harriet@plavex.co.uk
Address: Brackwell House
Fenmoor Enterprise Park
Partridge Way
Norwich
QB9 3KX
Tel:01632 960418

```html
<!DOCTYPE html>
<html lang="en">
<head>
<meta charset="utf-8">
<title>Plavex – Business Card</title>
<link rel="stylesheet" href="https://fonts.googleapis.com/css2?family=Quicksand:wght@500;600;700&display=swap">
<style>
  :root {
    --backdrop: #e6e3e0;
    --card: #ffffff;
    --ink-grey: #7d7a7e;
    --ink-soft: #8e8b8f;
    --brand-green: #8cc414;
    --rule: #d9d7d9;
    --shadow: rgba(60, 55, 50, 0.16);
  }
  * { box-sizing: border-box; margin: 0; padding: 0; }
  html, body {
    width: 1200px;
    height: 997px;
    overflow: hidden;
    background: var(--backdrop);
    font-family: "Quicksand", sans-serif;
  }
  .canvas {
    position: relative;
    width: 1200px;
    height: 997px;
  }
  .card {
    position: absolute;
    width: 510px;
    height: 292px;
    background: var(--card);
    border-radius: 3px;
    box-shadow: 0 6px 18px var(--shadow);
    overflow: hidden;
  }
  .card--contact { left: 80px; top: 180px; }
  .card--brand   { left: 610px; top: 520px; }

  /* Contact side */
  .identity {
    position: absolute;
    right: 272px;
    top: 108px;
    text-align: right;
  }
  .identity__name {
    font-weight: 700;
    font-size: 23px;
    letter-spacing: 0.5px;
    color: var(--ink-grey);
    text-transform: uppercase;
  }
  .identity__role {
    margin-top: 2px;
    font-weight: 600;
    font-size: 14px;
    color: var(--brand-green);
  }
  .divider {
    position: absolute;
    left: 250px;
    top: 70px;
    width: 1px;
    height: 128px;
    background: var(--rule);
  }
  .contact {
    position: absolute;
    left: 268px;
    top: 74px;
    list-style: none;
    font-weight: 500;
    font-size: 13px;
    line-height: 19px;
    color: var(--ink-soft);
  }
  .contact__item { display: flex; align-items: center; gap: 6px; }
  .contact__icon { width: 10px; height: 10px; fill: var(--brand-green); flex: none; }

  /* Brand side */
  .brand {
    position: absolute;
    left: 0;
    right: 0;
    top: 112px;
    display: flex;
    align-items: center;
    justify-content: center;
    gap: 14px;
  }
  .brand__dot {
    width: 46px;
    height: 46px;
    border-radius: 50%;
    background: var(--ink-grey);
  }
  .brand__text { display: flex; flex-direction: column; }
  .brand__name {
    font-weight: 700;
    font-size: 48px;
    line-height: 48px;
    color: var(--brand-green);
  }
  .brand__tagline {
    margin-top: 2px;
    font-weight: 500;
    font-size: 10px;
    letter-spacing: 3px;
    color: var(--ink-soft);
  }
</style>
</head>
<body>
<main class="canvas">
  <section class="card card--contact" aria-label="Business card, contact side">
    <div class="identity">
      <p class="identity__name">Harriet Dunmore</p>
      <p class="identity__role">President</p>
    </div>
    <div class="divider"></div>
    <ul class="contact">
      <li class="contact__item">
        <svg class="contact__icon" viewBox="0 0 10 10" aria-hidden="true"><path d="M2 0.5l1.6 2.2-1 1a6 6 0 0 0 3.7 3.7l1-1L9.5 8 8.3 9.5C4 9.2 0.8 6 0.5 1.7z"/></svg>
        01632 960418
      </li>
      <li class="contact__item">
        <svg class="contact__icon" viewBox="0 0 10 10" aria-hidden="true"><path d="M0.5 2h9v6h-9z M0.5 2l4.5 3.5L9.5 2" stroke="#fff" stroke-width="0.8"/></svg>
        Harriet@plavex.co.uk
      </li>
      <li>Brackwell House</li>
      <li>Fenmoor Enterprise Park</li>
      <li>Partridge Way Norwich QB9 3KX</li>
    </ul>
  </section>

  <section class="card card--brand" aria-label="Business card, brand side">
    <div class="brand">
      <span class="brand__dot" aria-hidden="true"></span>
      <div class="brand__text">
        <span class="brand__name">Plavex</span>
        <span class="brand__tagline">Technology Recruitment</span>
      </div>
    </div>
  </section>
</main>
</body>
</html>
```